Corporate Business Card

Very professional, Modern, Not to busy, include phone address email, website
(253) 617-4930, 18761 52nd Avenue S, Kent, WA 98047, martin@plumlinegroup.com, varkoworks.com

Target Market(s)

Manufacturing

Industry/Entity Type

Aero, machining, manufacturing, Off road racing

Contact Information for Business Card

Phone, address email, website

```html
<!DOCTYPE html>
<html lang="en">
<head>
<meta charset="utf-8">
<title>Varko Works – Business Card</title>
<link href="https://fonts.googleapis.com/css2?family=Lato:wght@400;700;900&family=Orbitron:wght@800&display=swap" rel="stylesheet">
<style>
  :root {
    --navy: #17366f;
    --red: #d4242c;
    --white: #ffffff;
    --ink: #444a52;
    --backdrop: #2b2b2b;
  }
  * { margin: 0; padding: 0; box-sizing: border-box; }
  html, body {
    width: 1200px; height: 1200px; overflow: hidden;
    background: var(--backdrop);
    font-family: "Lato", sans-serif;
  }
  .card {
    position: absolute; left: 250px;
    width: 700px; height: 400px; overflow: hidden;
  }
  .card-front { top: 170px; background: var(--white); }
  .card-back { top: 630px; background: var(--navy); }

  .brand-name {
    position: absolute; font-family: "Lato", sans-serif; font-weight: 900;
    letter-spacing: 2px; white-space: nowrap;
  }
  .card-front .brand-name {
    left: 55px; top: 152px; font-size: 34px; color: var(--navy);
  }
  .card-back .brand-name {
    left: 0; right: 0; top: 158px; text-align: center;
    font-size: 72px; color: var(--white); letter-spacing: 4px;
  }

  .person { position: absolute; left: 357px; top: 90px; }
  .person-name {
    font-family: "Orbitron", sans-serif; font-weight: 800; font-style: italic;
    font-size: 25px; color: var(--navy); letter-spacing: 1px; line-height: 1;
  }
  .person-title {
    margin-top: 6px; font-size: 19px; color: var(--red); line-height: 1.2;
  }

  .contact-list { position: absolute; left: 357px; top: 162px; list-style: none; }
  .contact-item {
    display: flex; align-items: flex-start; gap: 8px;
    font-size: 16px; color: var(--ink); line-height: 24px; letter-spacing: 0.4px;
  }
  .contact-item + .contact-item { margin-top: 0; }
  .contact-item.phone { margin-top: 4px; }
  .contact-icon { width: 14px; height: 14px; margin-top: 5px; flex: none; fill: var(--navy); }

  .web-band { position: absolute; left: 0; top: 344px; width: 700px; height: 56px; }
  .web-address {
    position: absolute; left: 103px; top: 350px;
    font-size: 16px; color: var(--white); letter-spacing: 4px; line-height: 24px;
  }
</style>
</head>
<body>

<section class="card card-front">
  <div class="brand-name">VARKO WORKS</div>

  <div class="person">
    <div class="person-name">AARON KESSLER</div>
    <div class="person-title">Managing Director</div>
  </div>

  <ul class="contact-list">
    <li class="contact-item">
      <svg class="contact-icon" viewBox="0 0 14 14" aria-hidden="true"><path d="M7 0a5 5 0 0 0-5 5c0 3.6 5 9 5 9s5-5.4 5-9a5 5 0 0 0-5-5zm0 7a2 2 0 1 1 0-4 2 2 0 0 1 0 4z"/></svg>
      <span>18761 52nd Avenue S<br>Kent, WA 98047</span>
    </li>
    <li class="contact-item phone">
      <svg class="contact-icon" viewBox="0 0 14 14" aria-hidden="true"><path d="M3 1l2.2 2.8-1.3 1.6c.8 1.8 2 3 3.8 3.8l1.6-1.3L12 10l-1.4 2.6C6 12.6 1.4 8 1.4 2.4z"/></svg>
      <span>(253) 617-4930</span>
    </li>
    <li class="contact-item">
      <svg class="contact-icon" viewBox="0 0 14 14" aria-hidden="true"><path d="M1 3.5h12v8H1z M1.6 4l5.4 4 5.4-4" stroke="#fff" stroke-width="0.8"/></svg>
      <span>martin@plumlinegroup.com</span>
    </li>
  </ul>

  <svg class="web-band" viewBox="0 0 700 56" aria-hidden="true">
    <rect width="700" height="56" fill="var(--navy)"/>
    <polygon points="0,35 524,35 566,0 580,0 574,37 700,37 700,41 569,41 573,4 527,41 0,41" fill="var(--white)"/>
    <polygon points="0,0 560,0 519,35 0,35" fill="var(--red)"/>
    <polygon points="585,0 700,0 700,36 579,36" fill="var(--red)"/>
  </svg>
  <div class="web-address">WWW.VARKOWORKS.COM</div>
</section>

<section class="card card-back">
  <div class="brand-name">VARKO WORKS</div>
</section>

</body>
</html>
```